Business Card Design

We would like to re-design our business cards. Our Company - Qwinrel Turbochargers, rebuilds turbochargers and sells replacement parts. Our website is: http://www.qwinrelturbochargers-example.com
We just had our logo changed. I will attach the file. Looking for fresh new/modern business card. We like the colors red, black, white and silver. Black background looks attractive, but not a requirement. The final design should communicate reasonable/competitive prices, top quality and reliability of our products.
Updates
Project Deadline Extended
Reason: Need to finalize the info on the card. Currently working on changing address and email info. Want to make sure it is the correct one before accepting the final design. Unless, this is something that can be changed at a later time..??
Industry/Entity Type
Business
Contact Information for Business Card
QWINREL TURBOCHARGERS, LLC
20473 Harwick Lane NE
Massillon, OH 44647
Tel: +1-555-214-7390
Fax: +1-555-267-1842
info@QwinrelTurbochargers-example.com
Our current business card had the following highlights:
*We rebuild all Turbocharges for Automotive, Diesel and Industrial
*Precision Balancing and in-house turbocharger needs
*All Turbocharger replacement parts are made in USA / U.K.
Look and feel
Each slider illustrates characteristics of the customer's brand and the style your logo design should communicate.

```html
<!DOCTYPE html>
<html lang="en">
<head>
<meta charset="utf-8">
<title>Qwinrel Turbochargers – Business Card</title>
<link href="https://fonts.googleapis.com/css2?family=Roboto+Condensed:wght@400;700&display=swap" rel="stylesheet">
<style>
  :root {
    --bg: #e9e7e4;
    --card: #f7f7f6;
    --ink: #2b2b2d;
    --charcoal: #2e2e30;
    --red: #e32430;
    --white: #ffffff;
  }
  html, body {
    margin: 0;
    width: 1200px;
    height: 902px;
    overflow: hidden;
    background: var(--bg);
    font-family: "Roboto Condensed", Arial, sans-serif;
  }
  .card {
    position: absolute;
    width: 540px;
    height: 309px;
    background: var(--card);
    box-shadow: 0 6px 18px rgba(0,0,0,.18);
    overflow: hidden;
  }
  .card--front { left: 60px; top: 110px; }
  .card--back { left: 600px; top: 480px; }
  .card__shapes { position: absolute; inset: 0; }
  .brand {
    position: absolute;
    display: flex;
    align-items: center;
    gap: 10px;
  }
  .brand__dot {
    width: 26px;
    height: 26px;
    border-radius: 50%;
    background: var(--red);
    flex: none;
  }
  .brand__name {
    font-weight: 700;
    color: var(--ink);
    font-size: 30px;
    line-height: 1;
    white-space: nowrap;
  }
  .card--front .brand { left: 92px; top: 104px; }
  .card--back .brand { left: 70px; top: 72px; }
  .card--back .brand__name { font-size: 26px; }
  .card--back .brand__dot { width: 22px; height: 22px; }
  .holder {
    position: absolute;
    right: 26px;
    top: 178px;
    text-align: right;
    color: var(--white);
  }
  .holder__name { font-weight: 700; font-size: 25px; line-height: 1; }
  .holder__title { font-size: 12px; margin-top: 3px; }
  .contacts {
    position: absolute;
    left: 24px;
    top: 196px;
    margin: 0;
    padding: 0;
    list-style: none;
    color: var(--white);
    font-size: 13px;
  }
  .contacts li {
    display: flex;
    align-items: center;
    gap: 9px;
    height: 20px;
  }
  .contacts li.contacts__cont { padding-left: 23px; height: 16px; margin-top: -3px; }
  .contacts svg { width: 14px; height: 14px; flex: none; }
</style>
</head>
<body>

<section class="card card--front" aria-label="Card front">
  <svg class="card__shapes" viewBox="0 0 540 309" aria-hidden="true">
    <polygon points="372,196 540,188 540,214 400,214" fill="var(--red)"/>
    <polygon points="0,262 300,262 345,224 540,224 540,309 0,309" fill="var(--charcoal)"/>
  </svg>
  <div class="brand">
    <span class="brand__dot"></span>
    <span class="brand__name">Qwinrel Turbochargers</span>
  </div>
</section>

<section class="card card--back" aria-label="Card back">
  <svg class="card__shapes" viewBox="0 0 540 309" aria-hidden="true">
    <polygon points="300,148 540,148 540,250 402,250" fill="var(--red)"/>
    <polygon points="0,183 330,183 465,309 0,309" fill="var(--charcoal)"/>
  </svg>
  <div class="brand">
    <span class="brand__dot"></span>
    <span class="brand__name">Qwinrel Turbochargers</span>
  </div>
  <div class="holder">
    <div class="holder__name">Employee name</div>
    <div class="holder__title">Managing Director</div>
  </div>
  <ul class="contacts">
    <li>
      <svg viewBox="0 0 14 14" aria-hidden="true"><rect width="14" height="14" fill="var(--white)"/><path d="M4 3l2 2-1 1.3a6 6 0 0 0 2.7 2.7L9 8l2 2-1.2 1.2C6.5 11 3 7.5 2.8 4.2z" fill="var(--red)"/></svg>
      555-214-7390
    </li>
    <li>
      <svg viewBox="0 0 14 14" aria-hidden="true"><rect width="14" height="14" fill="var(--white)"/><circle cx="7" cy="7" r="4" fill="none" stroke="var(--red)" stroke-width="1.4"/><path d="M3 7h8M7 3v8" stroke="var(--red)" stroke-width="1"/></svg>
      www.qwinrelturbochargers-example.com
    </li>
    <li>
      <svg viewBox="0 0 14 14" aria-hidden="true"><rect width="14" height="14" fill="var(--white)"/><rect x="2.5" y="4" width="9" height="6.5" fill="var(--red)"/><path d="M2.5 4L7 8l4.5-4" fill="none" stroke="var(--white)" stroke-width="1"/></svg>
      info@QwinrelTurbochargers-example.com
    </li>
    <li>
      <svg viewBox="0 0 14 14" aria-hidden="true"><rect width="14" height="14" fill="var(--white)"/><path d="M7 12S3.5 8 3.5 5.8a3.5 3.5 0 0 1 7 0C10.5 8 7 12 7 12z" fill="var(--red)"/><circle cx="7" cy="5.8" r="1.3" fill="var(--white)"/></svg>
      5218 Dorrance Ave.
    </li>
    <li class="contacts__cont">NW East Harwick, Ohio</li>
  </ul>
</section>

</body>
</html>
```